FunBrixo Business Card

We need a business card design for our company. We sell construction-themed amusement rides for kids.

Contact Information for Business Card

Contact info on business card should include:
Carl Dunning
Co-Founder & COO
(833) 571-FUNBRIX
Carl@funbrixo-demo.com
www.funbrixo-demo.com

```html
<!DOCTYPE html>
<html lang="en">
<head>
<meta charset="utf-8">
<title>FunBrixo Business Card</title>
<link rel="stylesheet" href="https://fonts.googleapis.com/css2?family=Arimo:wght@400;700&display=swap">
<style>
  :root {
    --page-bg: #e9e6e1;
    --card-white: #ffffff;
    --brand-orange: #e8562a;
    --ink: #1a1a1a;
    --band-black: #0d0d0d;
    --sky-top: #3f86c4;
    --sky-mid: #bcd3e2;
    --sunset: #f1b67a;
    --machine-orange: #e98d1e;
    --figure-skin: #9a6a45;
    --figure-blue: #4f86b8;
    --helmet-yellow: #f4c21b;
  }
  * { box-sizing: border-box; margin: 0; padding: 0; }
  html, body {
    width: 1200px; height: 900px; overflow: hidden;
    background: var(--page-bg);
    font-family: "Arimo", Arial, sans-serif;
  }
  .card {
    position: absolute;
    width: 620px; height: 354px;
    left: 290px;
    border-radius: 4px;
    overflow: hidden;
    box-shadow: 0 6px 18px rgba(0,0,0,0.18);
  }
  .card--front { top: 64px; }
  .card--back { top: 482px; background: var(--card-white); }

  /* Front side */
  .front-photo {
    position: absolute; inset: 0;
    background:
      linear-gradient(180deg, transparent 45%, rgba(233,141,30,0.85) 75%, var(--machine-orange) 100%),
      linear-gradient(180deg, var(--sky-top) 0%, var(--sky-mid) 30%, var(--sunset) 55%, #e7a466 100%);
  }
  .front-brand {
    position: absolute; left: 0; right: 0; top: 70px;
    text-align: center;
    font-weight: 700; font-size: 62px;
    color: var(--brand-orange);
    letter-spacing: 1px;
  }

  /* Back side */
  .back-wave { position: absolute; inset: 0; width: 620px; height: 354px; }
  .back-brand {
    position: absolute; left: 56px; top: 66px;
    font-weight: 700; font-size: 44px;
    color: var(--brand-orange);
  }
  .contact { position: absolute; left: 62px; top: 140px; color: var(--ink); }
  .contact__name {
    font-weight: 700; font-size: 22px;
    color: var(--brand-orange); text-transform: uppercase;
    letter-spacing: 0.5px;
  }
  .contact__role { font-size: 17px; margin-top: 2px; }
  .contact__list { list-style: none; margin-top: 14px; }
  .contact__item {
    display: flex; align-items: center; gap: 10px;
    font-size: 17px; line-height: 28px;
  }
  .contact__icon { width: 18px; height: 18px; flex: none; }
  .workers-art {
    position: absolute; left: 392px; top: 30px;
    width: 180px; height: 180px;
    border-radius: 8px;
    background: linear-gradient(180deg, var(--helmet-yellow) 0%, var(--figure-skin) 35%, var(--figure-blue) 70%, #f0f0f0 100%);
    opacity: 0.85;
  }
  .website {
    position: absolute; right: 34px; top: 224px;
    color: var(--card-white); font-size: 14px;
  }
</style>
</head>
<body>
  <section class="card card--front" aria-label="Card front">
    <div class="front-photo" role="img" aria-label="Photo of a kids' construction-themed ride park with orange mini excavators at sunset"></div>
    <div class="front-brand">FunBrixo</div>
  </section>

  <section class="card card--back" aria-label="Card back">
    <svg class="back-wave" viewBox="0 0 620 354" aria-hidden="true">
      <path d="M0,292 C160,318 300,286 410,236 C300,300 150,330 0,318 Z" fill="var(--brand-orange)"/>
      <path d="M0,318 C150,330 300,300 410,236 C490,198 560,186 620,182 L620,354 L0,354 Z" fill="var(--band-black)"/>
    </svg>

    <div class="back-brand">FunBrixo</div>

    <div class="workers-art" role="img" aria-label="Illustration of two cartoon construction workers in hard hats shaking hands"></div>

    <div class="contact">
      <p class="contact__name">Carl Dunning</p>
      <p class="contact__role">Co-Founder &amp; COO</p>
      <ul class="contact__list">
        <li class="contact__item">
          <svg class="contact__icon" viewBox="0 0 18 18" aria-hidden="true">
            <rect x="1" y="1" width="16" height="16" rx="3" fill="none" stroke="var(--brand-orange)" stroke-width="1.6"/>
            <path d="M6,4.5 L8,7 L7,8.3 C7.8,9.8 8.6,10.6 10,11.3 L11.3,10.3 L13.6,12.2 L12.4,13.7 C9,13.2 5.2,9.4 4.6,5.8 Z" fill="var(--brand-orange)"/>
          </svg>
          (833) 571-FUNBRIX
        </li>
        <li class="contact__item">
          <svg class="contact__icon" viewBox="0 0 18 18" aria-hidden="true">
            <rect x="1" y="4" width="16" height="11" fill="var(--brand-orange)"/>
            <path d="M1,4 L9,10.5 L17,4" fill="none" stroke="#fff" stroke-width="1.4"/>
          </svg>
          Carl@funbrixo-demo.com
        </li>
      </ul>
    </div>

    <p class="website">www.funbrixo-demo.com</p>
  </section>
</body>
</html>
```